Business Card Design Project

Business Card
We are rebranding with a new logo
Industry/Entity Type
Business
Contact Information for Business Card
Dennis Morvale +61 487215963 dennis@quorv.com.au P.O. Box 872 Fernlow QLD 4309
Requirements
Must have
- Logo

```html
<!DOCTYPE html>
<html lang="en">
<head>
<meta charset="utf-8">
<title>Quorv International — Business Card</title>
<link rel="stylesheet" href="https://fonts.googleapis.com/css2?family=Dancing+Script:wght@700&family=Roboto:wght@400;700&display=swap">
<style>
  :root {
    --backdrop: #dcdcdc;
    --card: #f6f6f6;
    --card-edge: #ececec;
    --navy: #16506f;
    --ink: #1c1c1c;
    --accent: #e2682c;
    --brand-ink: #1f3f5a;
  }
  * { box-sizing: border-box; margin: 0; padding: 0; }
  html, body {
    width: 1200px; height: 576px; overflow: hidden;
    background: var(--backdrop);
    font-family: "Roboto", Arial, sans-serif;
  }
  .canvas { position: relative; width: 1200px; height: 576px; }
  .card {
    position: absolute; top: 138px; width: 484px; height: 293px;
    border-radius: 14px;
    background: linear-gradient(180deg, var(--card) 0%, var(--card-edge) 100%);
    box-shadow: 0 2px 4px rgba(0,0,0,0.18);
  }
  .card--front { left: 82px; }
  .card--back { left: 602px; }

  .brand { position: absolute; text-align: center; color: var(--brand-ink); font-weight: 700; line-height: 1; }
  .brand__name { display: block; font-size: 52px; letter-spacing: 1px; }
  .brand__tag { display: block; font-size: 15px; letter-spacing: 3px; margin-top: 8px; }
  .card--front .brand { left: 0; right: 0; top: 98px; }
  .card--back .brand { right: 32px; top: 220px; width: 150px; }
  .card--back .brand__name { font-size: 38px; }
  .card--back .brand__tag { font-size: 11px; letter-spacing: 2px; margin-top: 6px; }

  .holder { position: absolute; left: 26px; top: 36px; }
  .holder__name {
    font-family: "Dancing Script", cursive; font-weight: 700;
    font-size: 26px; color: var(--navy); line-height: 1;
  }
  .holder__role { font-size: 11px; color: var(--ink); margin-top: 6px; }

  .contacts { position: absolute; left: 26px; top: 213px; list-style: none; }
  .contacts li { display: flex; align-items: center; height: 17px; font-size: 12px; color: var(--ink); }
  .contacts svg { width: 12px; height: 12px; margin-right: 12px; fill: var(--accent); }
</style>
</head>
<body>
<div class="canvas">
  <section class="card card--front">
    <div class="brand">
      <span class="brand__name">Quorv</span>
      <span class="brand__tag">INTERNATIONAL</span>
    </div>
  </section>

  <section class="card card--back">
    <div class="holder">
      <p class="holder__name">Dennis Morvale</p>
      <p class="holder__role">Managing Director</p>
    </div>
    <ul class="contacts">
      <li>
        <svg viewBox="0 0 12 12" aria-hidden="true"><path d="M1 3.5C1 2 3 1.5 6 1.5S11 2 11 3.5V5H8.5V4H3.5V5H1Z"/><rect x="2.5" y="6" width="7" height="4.5" rx="1"/></svg>
        +61 487215963
      </li>
      <li>
        <svg viewBox="0 0 12 12" aria-hidden="true"><path d="M1 2.5H11V9.5H1Z M1.8 3.3L6 6.6L10.2 3.3" stroke="#f6f6f6" stroke-width="0.9"/></svg>
        dennis@quorv.com.au
      </li>
      <li>
        <svg viewBox="0 0 12 12" aria-hidden="true"><path d="M6 0.5A4 4 0 0 1 10 4.5C10 7.5 6 11.5 6 11.5S2 7.5 2 4.5A4 4 0 0 1 6 0.5Z"/><circle cx="6" cy="4.5" r="1.5" fill="#f6f6f6"/></svg>
        P.O. Box 872 Fernlow QLD 4309
      </li>
    </ul>
    <div class="brand">
      <span class="brand__name">Quorv</span>
      <span class="brand__tag">INTERNATIONAL</span>
    </div>
  </section>
</div>
</body>
</html>
```